New B2C website design to help dads be better dads

DadHarbor is a website to help dads be the “best dad you can be.”

We require our website to be designed into a PSD format, no coding necessary.

The general concept is a two-page design. The first page is the login page, the second page is the home page. Once at the home page, rather than navigating to and from different pages, the user will push and pull through different visual and functional layers of the hierarchy. In theory, this should add to the user experience by having a visual anchor of where they are (through layered pagination) as well as improving loading times since the new information should only be a delta in data load versus a brand new page load.

The general look-and-feel we are going for is clean, simple, minimal. This means that the winning design will show us a good eye for web-optimized typography, good use of white (negative) space, and good use of a visually pleasing grid.

We require a total of 6 page "views" plus the landing page. We note that many of the views are similar to one another.
Landing page
Milestone view
Task view
Content view, articles
Content view, products
Search view
What's new view

Please review all of the additional information provided as well as the attachments for examples.

We provide the following websites as good references for:

Typography:
http://example-kelvorn.com/journal/

Use of white space:
http://www.trenvaskit.com/
http://moldrefin.com/

Example for “scrolling” page concept as well as good balance of color, typography, and white space:
http://www.qorbitalmeet.eu/

Please contact us with questions so that we can guide your design effort.
Updates

Hello designers,

The following information is added to help guide the design process:

1.  For the text dialogue below the landing page, please assume the following word count:
"why are we making dad harbor?": 250 words
"who are we?" 200 words
"what's the deal with the penguin logo?" 300 words

For the social media links, please see http://www.gravelplumbs.com/
Notice the floating "social" bar that is always to the right.  This is the concept we are going for, please try to implement this as you see fit. 

Target Market(s)

Fathers of young children ages 0-6 years old.

Industry/Entity Type

Product

Font styles to use
Sans Serif

Requirements
Must have
• Clean lines, minimal design concept

Incorporation of our logo (see attached document)

Header content is static for all views after landing page, see example

This page WILL be responsive, please keep that in mind when designing
The timeline bar should be to the left, with the timeline bar’s “milestones” also being responsive.

Designer is free to suggest font types, but any fonts used must be royalty-free and web-optimized. We request a minimum number of font types as well as fonts that load relatively fast. We reinforce that visually appealing typography is a significant factor in the winning design choice.

While we are not expecting the winning design to include code, please keep in mind that the final implementation needs to be optimized for desktop, tablet, and mobile platforms.

If you are using stock photography that is not generated by you, please provide where/how we can obtain imagery, as well as price.

All custom graphics must be available in original formats; Photoshop/GIMP layered files for layout design, and vector formats for logos, icons and other graphical elements.

Please incorporate “Blue” into design elements as you see fit, as the RGB 67 74 169 Blue is the primary color used in our brand. The complement to this blue is 255 202 0, a brownish orange. Feel free to use this color as well, although please keep it to a lesser amount.

Background color is your choice, do not feel the need to use the grey.
Should not have
• Excessive graphical content such that it affects loading times

Excessive use of too many font types such that it affects loading times

```html
<!DOCTYPE html>
<html lang="en">
<head>
<meta charset="utf-8">
<title>DadHarbor – Search view</title>
<link href="https://fonts.googleapis.com/css2?family=PT+Sans:wght@400;700&family=Rokkitt:wght@400;500&display=swap" rel="stylesheet">
<style>
  :root{
    --brand-blue:#434aa9;
    --brand-gold:#ffca00;
    --welcome-gold:#dc9c12;
    --text:#444;
    --muted:#777;
    --line:#d9d9d9;
    --page:#f8f8f8;
    --white:#fff;
  }
  *{box-sizing:border-box;margin:0;padding:0}
  html,body{width:818px;height:1200px;overflow:hidden}
  body{position:relative;background:var(--page);font-family:"PT Sans",sans-serif;color:var(--text)}
  .abs{position:absolute}

  /* header */
  .site-header{position:absolute;left:0;top:0;width:818px;height:128px;background:var(--white);border-bottom:1px solid var(--line)}
  .brand{position:absolute;left:68px;top:86px;display:flex;align-items:center;gap:8px;font-family:"PT Sans",sans-serif;font-weight:700;font-size:20px;color:var(--brand-blue);letter-spacing:.5px}
  .brand-dot{width:14px;height:14px;border-radius:50%;background:var(--brand-blue)}
  .welcome{position:absolute;right:68px;top:12px;font-family:"Rokkitt",serif;font-size:20px;color:var(--welcome-gold)}
  .search{position:absolute;left:479px;top:52px;display:flex;gap:6px}
  .search-input{width:208px;height:24px;border:1px solid #ccc;background:var(--white);font-size:10px;color:#999;padding:5px 10px}
  .search-button{width:52px;height:24px;background:var(--brand-gold);border:1px solid #e8b400;color:#8a5d00;font-size:10px;display:flex;align-items:center;justify-content:center}
  .dad-score{position:absolute;left:479px;top:95px;font-size:11px;color:var(--brand-blue);display:flex;align-items:center;gap:6px}
  .account-links{position:absolute;right:74px;top:95px;font-size:11px;color:var(--muted)}
  .account-links .sep{margin:0 6px;color:#aaa}

  /* timeline */
  .timeline-bar{position:absolute;left:68px;top:150px;width:1px;height:930px;background:#ccc}
  .milestone-row{position:absolute;left:68px;width:682px;border-bottom:1px solid var(--line)}
  .milestone-age{position:absolute;left:-28px;font-size:8px;color:#999}
  .milestone-dot{position:absolute;left:-4px;width:9px;height:9px}
  .milestone-title{position:absolute;left:22px;font-family:"Rokkitt",serif;color:#555}
  .sort{position:absolute;left:618px;top:150px;display:flex;align-items:center;gap:6px;font-size:9px;color:var(--muted)}
  .sort-select{width:94px;height:20px;border:1px solid #ccc;background:var(--white);font-size:9px;color:#333;padding:4px 8px;position:relative}
  .sort-select::after{content:"";position:absolute;right:7px;top:8px;border:3px solid transparent;border-top:4px solid #444}

  /* task filter */
  .task-filter{position:absolute;left:90px;top:307px;width:165px;height:249px;background:var(--white);border:1px solid var(--line);padding:6px 7px}
  .task-item{height:30px;display:flex;align-items:center;gap:8px;font-size:10px;color:#333;border-bottom:1px solid #eee;padding-left:10px}
  .task-item:last-child{border-bottom:none}
  .check{width:8px;height:8px;border:1px solid #aaa;background:#f4f4f4;position:relative}

  /* results */
  .results-heading{position:absolute;left:268px;width:479px;top:325px;text-align:center;font-family:"Rokkitt",serif;font-size:15px;color:#333}
  .results-grid{position:absolute;left:268px;top:356px;display:grid;grid-template-columns:230px 230px;column-gap:20px;row-gap:21px}
  .result-card{height:256px;background:var(--white);border:1px solid var(--line);padding:4px;position:relative}
  .result-photo{height:124px;position:relative}
  .tone-a{background:linear-gradient(135deg,#3b3f46,#8b8f98 60%,#4a4d55)}
  .tone-b{background:linear-gradient(135deg,#6b5e52,#c9bba8 55%,#4f4640)}
  .tone-c{background:linear-gradient(135deg,#a8562e,#d9a77a 50%,#5c4537)}
  .tone-d{background:linear-gradient(180deg,#3c3e44,#c9a89b 55%,#3a3b40)}
  .tone-e{background:linear-gradient(135deg,#59626a,#b7c0c6 55%,#6f777d)}
  .tone-f{background:linear-gradient(135deg,#3e2a22,#c69d86 55%,#d7dde4)}
  .type-badge{position:absolute;right:2px;bottom:2px;width:26px;height:26px;background:var(--brand-gold);display:flex;align-items:center;justify-content:center}
  .result-title{font-family:"Rokkitt",serif;font-size:12.5px;line-height:16px;color:var(--brand-blue);margin:10px 7px 0}
  .rating{display:flex;align-items:center;gap:1px;margin:8px 7px 0;font-size:9.5px;color:#666}
  .rating .count{margin-left:8px}
  .result-excerpt{font-size:9.5px;line-height:16px;color:#666;margin:9px 7px 0}
  .read-more{color:var(--brand-blue);white-space:nowrap}
  .page-end{position:absolute;left:0;top:1197px;width:818px;height:1px;background:var(--line)}
</style>
</head>
<body>

<header class="site-header">
  <div class="brand"><span class="brand-dot"></span>DADHARBOR</div>
  <div class="welcome">Welcome Tomas, what would you like to do today?</div>
  <div class="search">
    <div class="search-input">Keyword...</div>
    <div class="search-button">SEARCH</div>
  </div>
  <div class="dad-score">
    <svg width="9" height="8" viewBox="0 0 10 9"><path d="M5 9 L0.8 4.6 A2.4 2.4 0 0 1 5 1.6 A2.4 2.4 0 0 1 9.2 4.6 Z" fill="#434aa9"/></svg>
    Super Dad Score: 10,500
  </div>
  <div class="account-links">My Account<span class="sep">|</span>Log out</div>
</header>

<div class="timeline-bar"></div>

<section class="milestone-row" style="top:150px;height:44px">
  <span class="milestone-age" style="top:8px">-3 mo</span>
  <svg class="milestone-dot" style="top:9px" viewBox="0 0 10 10"><circle cx="5" cy="5" r="5" fill="#555"/><path d="M4 3 L6.5 5 L4 7" stroke="#fff" stroke-width="1.2" fill="none"/></svg>
  <h2 class="milestone-title" style="top:0;font-size:18px">Prepare for the baby arrival</h2>
</section>
<div class="sort">Sort by : <div class="sort-select">Most recent</div></div>

<section class="milestone-row" style="top:194px;height:56px">
  <span class="milestone-age" style="top:20px">0 mo</span>
  <svg class="milestone-dot" style="top:21px" viewBox="0 0 10 10"><circle cx="5" cy="5" r="5" fill="#555"/><path d="M4 3 L6.5 5 L4 7" stroke="#fff" stroke-width="1.2" fill="none"/></svg>
  <h2 class="milestone-title" style="top:15px;font-size:14.5px">What’s the Latest?</h2>
</section>

<section class="milestone-row" style="top:250px;height:57px">
  <span class="milestone-age" style="top:21px">0 mo</span>
  <svg class="milestone-dot" style="top:22px" viewBox="0 0 10 10"><circle cx="5" cy="5" r="5" fill="#555"/><path d="M4 3 L6.5 5 L4 7" stroke="#fff" stroke-width="1.2" fill="none"/></svg>
  <h2 class="milestone-title" style="top:16px;font-size:14.5px">What you searched for</h2>
</section>

<aside class="task-filter">
  <div class="task-item"><span class="check"></span>Buy a crib</div>
  <div class="task-item"><span class="check"></span>Assemble the crib</div>
  <div class="task-item"><span class="check"></span>Buy a stroller</div>
  <div class="task-item"><span class="check"><svg class="abs" style="left:0;top:-1px" width="8" height="8" viewBox="0 0 8 8"><path d="M1 4 L3 6 L7 1" stroke="#434aa9" stroke-width="1.3" fill="none"/></svg></span>Buy a carseat</div>
  <div class="task-item"><span class="check"></span>Install a carseat</div>
  <div class="task-item"><span class="check"></span>Learn to change a diaper</div>
  <div class="task-item"><span class="check"></span>Learn to hold a baby</div>
  <div class="task-item"><span class="check"></span>Set a fedding schedule</div>
</aside>

<h3 class="results-heading">Milestones and tasks related to your search :</h3>

<svg width="0" height="0" style="position:absolute">
  <defs>
    <symbol id="star" viewBox="0 0 10 10"><path d="M5 0.4 L6.3 3.5 L9.7 3.7 L7.1 5.9 L7.9 9.3 L5 7.5 L2.1 9.3 L2.9 5.9 L0.3 3.7 L3.7 3.5 Z" fill="#ffc20e"/></symbol>
    <symbol id="star-half" viewBox="0 0 10 10"><path d="M5 0.4 L6.3 3.5 L9.7 3.7 L7.1 5.9 L7.9 9.3 L5 7.5 L2.1 9.3 L2.9 5.9 L0.3 3.7 L3.7 3.5 Z" fill="none" stroke="#ffc20e" stroke-width=".8"/><path d="M5 0.4 L5 7.5 L2.1 9.3 L2.9 5.9 L0.3 3.7 L3.7 3.5 Z" fill="#ffc20e"/></symbol>
    <symbol id="icon-article" viewBox="0 0 16 16"><path d="M3 2 H11 L13 4 V14 H3 Z" fill="#111"/><path d="M10 2 V5 H13" fill="none" stroke="#ffca00" stroke-width=".8"/></symbol>
    <symbol id="icon-cart" viewBox="0 0 18 16"><path d="M1 2 H4 L6 11 H15 L17 5 H5" fill="none" stroke="#111" stroke-width="1.6"/><path d="M6.5 7 H15.5 M6 9 H15" stroke="#111" stroke-width="1"/><circle cx="7" cy="13.5" r="1.4" fill="#111"/><circle cx="14" cy="13.5" r="1.4" fill="#111"/></symbol>
  </defs>
</svg>

<main class="results-grid">
  <article class="result-card">
    <div class="result-photo tone-a" role="img" aria-label="Photo of a baby in a car seat playing with a hanging toy"><span class="type-badge"><svg width="16" height="16"><use href="#icon-article"/></svg></span></div>
    <h4 class="result-title">Pellentesque habitant morbi tristique senectus et netus</h4>
    <div class="rating"><svg width="12" height="12"><use href="#star"/></svg><svg width="12" height="12"><use href="#star"/></svg><svg width="12" height="12"><use href="#star"/></svg><svg width="12" height="12"><use href="#star"/></svg><svg width="12" height="12"><use href="#star-half"/></svg><span class="count">3,121 ratings</span></div>
    <p class="result-excerpt">I went out to buy my first car seat and had to earn my PhD in car seats, Newtonian physics, and anti-stain technology··· <span class="read-more">⊕ Read More</span></p>
  </article>
  <article class="result-card">
    <div class="result-photo tone-b" role="img" aria-label="Photo of a smiling baby in an infant carrier"><span class="type-badge"><svg width="18" height="16"><use href="#icon-cart"/></svg></span></div>
    <h4 class="result-title">Pellentesque habitant morbi tristique senectus et netus</h4>
    <div class="rating"><svg width="12" height="12"><use href="#star"/></svg><svg width="12" height="12"><use href="#star"/></svg><svg width="12" height="12"><use href="#star"/></svg><svg width="12" height="12"><use href="#star"/></svg><svg width="12" height="12"><use href="#star-half"/></svg><span class="count">3,121 ratings</span></div>
    <p class="result-excerpt">I went out to buy my first car seat and had to earn my PhD in car seats, Newtonian physics, and anti-stain technology··· <span class="read-more">⊕ Read More</span></p>
  </article>
  <article class="result-card">
    <div class="result-photo tone-c" role="img" aria-label="Photo of a toddler buckled into a car seat"><span class="type-badge"><svg width="16" height="16"><use href="#icon-article"/></svg></span></div>
    <h4 class="result-title">Pellentesque habitant morbi tristique senectus et netus</h4>
    <div class="rating"><svg width="12" height="12"><use href="#star"/></svg><svg width="12" height="12"><use href="#star"/></svg><svg width="12" height="12"><use href="#star"/></svg><svg width="12" height="12"><use href="#star"/></svg><svg width="12" height="12"><use href="#star-half"/></svg><span class="count">3,121 ratings</span></div>
    <p class="result-excerpt">I went out to buy my first car seat and had to earn my PhD in car seats, Newtonian physics, and anti-stain technology··· <span class="read-more">⊕ Read More</span></p>
  </article>
  <article class="result-card">
    <div class="result-photo tone-d" role="img" aria-label="Photo of a newborn strapped into a padded car seat"><span class="type-badge"><svg width="18" height="16"><use href="#icon-cart"/></svg></span></div>
    <h4 class="result-title">Pellentesque habitant morbi tristique senectus et netus</h4>
    <div class="rating"><svg width="12" height="12"><use href="#star"/></svg><svg width="12" height="12"><use href="#star"/></svg><svg width="12" height="12"><use href="#star"/></svg><svg width="12" height="12"><use href="#star"/></svg><svg width="12" height="12"><use href="#star-half"/></svg><span class="count">3,121 ratings</span></div>
    <p class="result-excerpt">I went out to buy my first car seat and had to earn my PhD in car seats, Newtonian physics, and anti-stain technology··· <span class="read-more">⊕ Read More</span></p>
  </article>
  <article class="result-card">
    <div class="result-photo tone-e" role="img" aria-label="Photo of a baby under a car seat belt"><span class="type-badge"><svg width="16" height="16"><use href="#icon-article"/></svg></span></div>
    <h4 class="result-title">Pellentesque habitant morbi tristique senectus et netus</h4>
    <div class="rating"><svg width="12" height="12"><use href="#star"/></svg><svg width="12" height="12"><use href="#star"/></svg><svg width="12" height="12"><use href="#star"/></svg><svg width="12" height="12"><use href="#star"/></svg><svg width="12" height="12"><use href="#star-half"/></svg><span class="count">3,121 ratings</span></div>
    <p class="result-excerpt">I went out to buy my first car seat and had to earn my PhD in car seats, Newtonian physics, and anti-stain technology··· <span class="read-more">⊕ Read More</span></p>
  </article>
  <article class="result-card">
    <div class="result-photo tone-f" role="img" aria-label="Photo of a sleeping baby in a car seat"><span class="type-badge"><svg width="18" height="16"><use href="#icon-cart"/></svg></span></div>
    <h4 class="result-title">Pellentesque habitant morbi tristique senectus et netus</h4>
    <div class="rating"><svg width="12" height="12"><use href="#star"/></svg><svg width="12" height="12"><use href="#star"/></svg><svg width="12" height="12"><use href="#star"/></svg><svg width="12" height="12"><use href="#star"/></svg><svg width="12" height="12"><use href="#star-half"/></svg><span class="count">3,121 ratings</span></div>
    <p class="result-excerpt">I went out to buy my first car seat and had to earn my PhD in car seats, Newtonian physics, and anti-stain technology··· <span class="read-more">⊕ Read More</span></p>
  </article>
</main>

<div class="page-end"></div>
</body>
</html>
```